“Professional 9x12 Pocket Folder Design – Roofing, Siding, Windows, Doors, Decks, Solar

✅ Page 1: Front Cover (Main Visual Impact)

Goal: Strong visual first impression representing all services Kelby’s Roofing offers.

Design Instructions:
• Top: Big, bold headline with Kelby’s Roofing (or company logo).
• Center: A high-quality image of a beautiful home that clearly shows:
• New roof (preferably dark shingles)
• Modern black-trim windows
• Upgraded front door
• Stylish siding (horizontal or board & batten)
• Visible garage door
• Optional: solar panels on the roof
• Optional: small composite front porch or deck
• Bottom Section (beneath the house image): Add keywords like:
Roofing • Siding • Windows • Doors • Decks • Solar • Local & Trusted

⸻

✅ Page 2: Back Cover

Goal: Tell the story of the company + display contact information for offices.

Design Instructions:
• Top Half: Section titled:
Our Story or About Kelby’s Roofing

Suggested Text (can be customized):
With over two decades of dedication to quality craftsmanship, Kelby’s Roofing has grown from a small local team into one of the region’s most trusted names in exterior home improvement. Our mission is to bring lasting beauty, energy efficiency, and protection to every home we touch.
• Bottom Half: Title:
Our Offices

Include up to 4 office addresses

Kelby's Roofing
2817 Tamarind St.
Stoughton, MA 02419
Kelby's Roofing
3390 Fenlow Ave, Warwick, RI 02715
Kelby's Roofing
716 N Ashdale St, Middleborough, MA 02193
Kelby's Roofing
4129 Pelland Hwy, East Wareham, MA 02467 ( Showroom )

⸻

✅ Inside Pockets

🔹 Left Pocket:

Title:

We’d Love Your Feedback

Text Suggestion:

Enjoyed your experience? Please leave us a review. Your feedback helps us grow and serve others better.

Add a QR code linking to the review page.for rateloop reviews

🔹 Right Pocket:

Your Product Specialist
Tobin Vasquel
📞 B:781-555-0142
P:774-555-0187
✉️ tvasquel@kelbyroofco.example

Let this info be printed/stamped directly on the folder, not using business cards
Our website https://kelbyroofco.example/?sfw=pass1751118580#

Feel free to take pictures from the website and use anything that is needed .

If we can add a flyer extra I’ll be willing to pay for that separate .
✅ Flyer Insert #1 (Double-Sided)

🔹 SIDE A: “Before & After Showcase”
• 4 Sections (lined up cleanly):
• Roofing
• Windows
• Skylights
• Decks
Each section includes:
• 📸 Before / After photo
• ✍️ Small description of the job (town + result)

🔹 SIDE B: “The Project Journey”

“What to Expect When You Work with Tobin”

• Step 1: Free Home Visit & Consultation
• Step 2: Custom Design Solutions
• Step 3: Quality Installation by Experts
• Step 4: Final Walkthrough + Satisfaction Check
• Soft closing line

Please use our best before and after pictures and take the data from Kelbyroofco.example

```html
<!DOCTYPE html>
<html lang="en">
<head>
<meta charset="utf-8">
<title>Kelby’s Roofing – Flyer Insert</title>
<link rel="stylesheet" href="https://fonts.googleapis.com/css2?family=Montserrat:wght@400;500;600&family=Oswald:wght@600&display=swap">
<style>
:root{
  --navy:#2b3580;
  --gold:#d4c68b;
  --gold-page:#d8c887;
  --ink:#2a2a2a;
  --white:#ffffff;
  --stage:#cbcbcb;
  --line:#555a66;
}
*{margin:0;padding:0;box-sizing:border-box}
html,body{width:1200px;height:884px;overflow:hidden}
body{background:var(--stage);font-family:"Montserrat",sans-serif;position:relative}
.page{position:absolute;top:79px;width:512px;height:725px;overflow:hidden}
.page--journey{left:78px;background:var(--white)}
.page--showcase{left:610px;background:var(--gold-page)}
.abs{position:absolute}
.photo{position:absolute}

/* Journey page */
.journey-box{left:27px;top:27px;width:234px;height:193px;background:var(--navy);color:var(--white);padding:22px 14px 0 21px}
.journey-box h2{font-size:10.8px;font-weight:600;margin-bottom:11px}
.journey-box p{font-size:9.6px;line-height:12px;font-weight:400;width:198px}
.journey-photo{left:248px;top:51px;width:235px;height:204px;background:linear-gradient(180deg,#8fb3e0 0%,#c9d6e6 30%,#8a8d6e 55%,#3f5a2c 100%)}

.step-tab{position:absolute;width:66px;height:32px;font-size:16px;font-weight:500;display:flex;align-items:center;justify-content:center}
.step-tab--navy{background:var(--navy);color:var(--white)}
.step-tab--gold{background:var(--gold);color:var(--ink)}
.step-text{position:absolute;font-size:15px;line-height:17px;color:var(--ink);font-weight:400}
.step-icon{position:absolute;width:18px;height:18px}

.expect-title{left:192px;top:381px;font-size:15.5px;font-weight:600;color:var(--navy);white-space:nowrap}
.expect-box{left:186px;top:400px;width:126px;height:49px;background:var(--gold);transform:rotate(-1.5deg);color:var(--ink);font-size:14.5px;font-weight:500;line-height:16.5px;text-align:center;display:flex;align-items:center;justify-content:center}
.connectors{position:absolute;left:0;top:0}

.contact-band{left:27px;top:618px;width:461px;height:85px;background:linear-gradient(90deg,var(--navy) 0%,var(--navy) 48%,#4a5590 70%,#8e8f9e 100%);clip-path:polygon(0 0,432px 0,461px 22px,461px 100%,0 100%)}
.contact-band h3{position:absolute;left:33px;top:13px;font-size:13px;font-weight:600;color:var(--white)}
.contact-list{position:absolute;left:33px;top:36px;list-style:none;color:var(--white);font-size:10.6px;line-height:13.4px}
.contact-list li{display:flex;align-items:center;gap:6px}
.contact-list svg{width:9px;height:9px;flex:none}
.quote-btn{position:absolute;left:204px;top:36px;width:135px;height:25px;background:var(--gold);color:var(--ink);font-size:13.5px;font-weight:500;display:flex;align-items:center;justify-content:center}

/* Showcase page */
.headline{position:absolute;left:36px;font-family:"Oswald",sans-serif;font-weight:600;font-size:46px;line-height:1;letter-spacing:-1px;transform:scaleX(.65);transform-origin:left top;white-space:nowrap}
.headline--1{top:32px;color:var(--navy)}
.headline--2{top:81px;color:var(--ink)}
.headline-strip{left:24px;top:134px;width:250px;height:71px;background:var(--white);transform:rotate(-4deg);transform-origin:left top;box-shadow:0 2px 4px rgba(0,0,0,.12)}
.headline--3{left:44px;top:141px;color:var(--navy);font-size:57px;transform:rotate(-4deg) scaleX(.51)}
.brand-name{position:absolute;left:312px;top:100px;width:164px;text-align:center;font-size:17px;font-weight:600;color:var(--navy)}

.photo-pair{position:absolute;background:var(--white);padding:2px;display:flex;gap:2px}
.photo-pair .photo{position:static;flex:1}
.service{position:absolute;width:142px;padding:10px 6px 6px 9px}
.service h4{font-size:9.6px;font-weight:600;margin-bottom:5px}
.service p{font-size:8.6px;line-height:10.4px;letter-spacing:-0.1px}
.service--navy{background:var(--navy);color:var(--white);clip-path:polygon(0 0,128px 0,142px 12px,142px 100%,0 100%)}
.service--white{background:var(--white);color:var(--ink);padding-left:17px;width:138px;clip-path:polygon(12px 0,100% 0,100% 100%,0 100%,0 12px)}
</style>
</head>
<body>

<section class="page page--journey">
  <div class="abs journey-box">
    <h2>Our Journey</h2>
    <p>Darren Whitcombe owner of Kelby’s Quality Roofing, Siding &amp; Windows likes to fix things. Not just leaky roofs, broken siding and drafty windows. When his personal experiences with home improvement contractors left him frustrated with their unreliability and shoddy work, he decided that the home improvement industry itself was in need of repair.</p>
  </div>
  <div class="photo journey-photo" role="img" aria-label="Photo of a tall sage green Victorian house with steep roof, chimneys and shrubs under a blue sky"></div>

  <svg class="connectors" width="512" height="725" aria-hidden="true">
    <g fill="none" stroke="var(--line)" stroke-width="0.8">
      <polyline points="127,297 225,297 225,374"/>
      <polyline points="334,304 325,304 325,424 316,424"/>
      <polyline points="127,504 153,504 153,391 178,391"/>
      <polyline points="251,456 251,511 283,511"/>
    </g>
  </svg>

  <div class="step-tab step-tab--navy" style="left:48px;top:282px">Step 1</div>
  <svg class="step-icon" style="left:48px;top:334px" viewBox="0 0 20 20" aria-hidden="true"><path d="M10 2 1 10h3v8h4v-5h4v5h4v-8h3z" fill="var(--navy)"/></svg>
  <p class="step-text" style="left:73px;top:326px">Free Home Visit<br>&amp; Consultation</p>

  <div class="step-tab step-tab--gold" style="left:341px;top:284px">Step 2</div>
  <svg class="step-icon" style="left:341px;top:330px" viewBox="0 0 20 20" aria-hidden="true"><g stroke="var(--gold)" stroke-width="2.2" stroke-linecap="round"><path d="M4 4l12 12"/><path d="M16 3l-11 11"/><path d="M3 17l3-3"/></g></svg>
  <p class="step-text" style="left:368px;top:328px">Custom Design<br>Solutions</p>

  <p class="abs expect-title">What to Expect</p>
  <div class="abs expect-box">When You<br>Work with Tobin</div>

  <div class="step-tab step-tab--gold" style="left:48px;top:489px">Step 3</div>
  <svg class="step-icon" style="left:48px;top:536px" viewBox="0 0 20 20" aria-hidden="true"><circle cx="12" cy="5" r="3.5" fill="var(--gold)"/><path d="M6 18c0-5 3-8 6-8s6 3 6 8z" fill="var(--gold)"/><circle cx="5" cy="14" r="3" fill="none" stroke="var(--gold)" stroke-width="1.6"/></svg>
  <p class="step-text" style="left:73px;top:533px">Quality Installation<br>by Experts</p>

  <div class="step-tab step-tab--navy" style="left:293px;top:491px">Step 4</div>
  <svg class="step-icon" style="left:292px;top:538px" viewBox="0 0 20 20" aria-hidden="true"><circle cx="10" cy="10" r="9" fill="var(--navy)"/><path d="M6 10.5l3 3 5-6" fill="none" stroke="var(--white)" stroke-width="2"/></svg>
  <p class="step-text" style="left:317px;top:535px">Final Walkthrough +<br>Satisfaction Check<br>Soft closing line</p>

  <div class="abs contact-band" role="img" aria-label="Contact band fading into a photo of a beige colonial house">
    <h3>Contact Us!</h3>
    <ul class="contact-list">
      <li><svg viewBox="0 0 10 10" aria-hidden="true"><path d="M2 1l2 0 1 2.5-1.2 1a5 5 0 0 0 2.7 2.7l1-1.2L10 7v2c0 .6-.5 1-1 1A9 9 0 0 1 0 2c0-.5.4-1 1-1z" fill="var(--gold)"/></svg>781.555.0199</li>
      <li><svg viewBox="0 0 10 10" aria-hidden="true"><path d="M1 0l8 5-3.5.8L7.5 10 6 10.5 4 6.3 1 9z" fill="var(--gold)"/></svg>kelbyroofco.example</li>
      <li><svg viewBox="0 0 10 10" aria-hidden="true"><rect x="0" y="1.5" width="10" height="7" fill="var(--gold)"/><path d="M0 1.5l5 4 5-4" fill="none" stroke="var(--navy)" stroke-width="1"/></svg>info@kelbyroofco.example</li>
    </ul>
    <div class="quote-btn">Request A Quote</div>
  </div>
</section>

<section class="page page--showcase">
  <p class="headline headline--1">Let’s Work Together,</p>
  <div class="abs headline-strip"></div>
  <p class="headline headline--2">to Create the</p>
  <p class="headline headline--3">Home You Deserve.</p>
  <p class="brand-name">Kelby’s Roofing</p>

  <div class="photo-pair" style="left:35px;top:220px;width:300px;height:108px">
    <div class="photo" role="img" aria-label="Before: cape house with grey shingle roof and skylights" style="background:linear-gradient(180deg,#5a84c4 0%,#9aa6b8 45%,#e6dccb 75%,#6b7a4a 100%)"></div>
    <div class="photo" role="img" aria-label="After: roof with new blue shingles seen from above" style="background:linear-gradient(160deg,#4f86c6 0%,#6ea0d4 55%,#c8bfa8 100%)"></div>
  </div>
  <div class="service service--navy" style="left:335px;top:236px;min-height:85px">
    <h4>Roofing</h4>
    <p>We offer a wide range of roofing services throughout the area. From replacements to repairs &amp; maintenance work.</p>
  </div>

  <div class="service service--white" style="left:37px;top:354px;min-height:86px">
    <h4>Windows</h4>
    <p>The windows were replaced with fiberglass mesh screens on vented windows with no grids.</p>
  </div>
  <div class="photo-pair" style="left:175px;top:342px;width:299px;height:108px">
    <div class="photo" role="img" aria-label="Before: old bay window with pink frames on grey siding" style="background:linear-gradient(180deg,#4d5866 0%,#8a6c72 55%,#4e6a3a 100%)"></div>
    <div class="photo" role="img" aria-label="After: new white bay window on blue grey siding" style="background:linear-gradient(180deg,#3e4b5a 0%,#e8ecef 45%,#5d7fa8 70%,#3b4a5a 100%)"></div>
  </div>

  <div class="photo-pair" style="left:35px;top:463px;width:300px;height:107px">
    <div class="photo" role="img" aria-label="Before: colonial house with dark roof and beige siding" style="background:linear-gradient(180deg,#4f86cc 0%,#8fa0b4 35%,#d9cdb4 65%,#4e6b35 100%)"></div>
    <div class="photo" role="img" aria-label="After: white cape house with navy roof and new skylights" style="background:linear-gradient(180deg,#8fb0d6 0%,#2f3a5a 40%,#eef0f2 65%,#5f9a3a 100%)"></div>
  </div>
  <div class="service service--navy" style="left:335px;top:475px;min-height:86px">
    <h4>Skylights</h4>
    <p>Kelby’s Roofing is proud to be a certified installer of Skyvane skylights. For over sixty years, Skyvane has been a leader in skylight &amp; roof light solutions.</p>
  </div>

  <div class="service service--white" style="left:37px;top:593px;min-height:86px">
    <h4>Decks</h4>
    <p>With years of experience &amp; excellent results to show for, you’ll want to look no further than us for your decking needs.</p>
  </div>
  <div class="photo-pair" style="left:175px;top:583px;width:298px;height:108px">
    <div class="photo" role="img" aria-label="Before: wooden deck frame with bare boards beside grey siding" style="background:linear-gradient(180deg,#9aa4b0 0%,#c97b3e 60%,#a5582a 100%)"></div>
    <div class="photo" role="img" aria-label="After: finished composite deck with white railings by a tan house" style="background:linear-gradient(180deg,#c9bb8a 0%,#eae6dc 40%,#6b4a3c 70%,#5a3e33 100%)"></div>
  </div>
</section>

</body>
</html>
```